A clean crisp business card for a Landscape Construction company. Designed to be easy to read contact/ info and also be appealing/interesting, unlike a traditional business card.

Industry/Entity Type

Landscape Construction

Contact Information for Business Card

Company name : Brambleford Landscape Construction, phone number: (555) 62Vista, website:Bramblefordyards.example, Email, sales@bramblefordyards.example

Requirements
Nice to have
• Luxurious finishes/ details…. Icons or emblems next to contact info
Should not have
• Clipart or general pictures

```html
<!DOCTYPE html>
<html lang="en">
<head>
<meta charset="utf-8">
<title>Brambleford Landscape Construction – Business Card</title>
<link href="https://fonts.googleapis.com/css2?family=Cinzel:wght@600&family=Arimo:wght@400&display=swap" rel="stylesheet">
<style>
  :root {
    --backdrop: #b1b1ab;
    --card: #030303;
    --edge: #8cc63f;
    --brand-blue: #1f5fbf;
    --brand-green: #8cc63f;
    --ink-light: #f2f2f2;
  }
  * { box-sizing: border-box; margin: 0; padding: 0; }
  html, body { width: 1200px; height: 801px; overflow: hidden; }
  body {
    background: var(--backdrop);
    position: relative;
    font-family: "Arimo", Arial, sans-serif;
  }
  .card {
    position: absolute;
    top: 250px;
    width: 540px;
    height: 300px;
    background: var(--card);
    box-shadow: 0 5px 0 var(--edge), 0 14px 24px rgba(0,0,0,0.3);
  }
  .card--back { left: 40px; }
  .card--front { left: 620px; }

  /* back side */
  .identity {
    position: absolute;
    left: 40px;
    top: 112px;
    text-align: right;
    width: 230px;
  }
  .identity__name {
    font-family: "Cinzel", "Times New Roman", serif;
    font-weight: 600;
    font-size: 27px;
    color: var(--brand-blue);
    letter-spacing: 0.5px;
    line-height: 1.1;
  }
  .identity__role {
    font-family: "Cinzel", "Times New Roman", serif;
    font-weight: 600;
    font-size: 18px;
    color: var(--brand-green);
    letter-spacing: 0.5px;
  }
  .divider {
    position: absolute;
    left: 284px;
    top: 100px;
    width: 1px;
    height: 84px;
    background: var(--brand-blue);
  }
  .contact {
    position: absolute;
    left: 298px;
    top: 102px;
    list-style: none;
  }
  .contact__item {
    display: flex;
    align-items: center;
    gap: 6px;
    color: var(--ink-light);
    font-size: 13px;
    line-height: 27px;
    white-space: nowrap;
  }
  .contact__icon { width: 11px; height: 11px; flex: none; }

  /* front side */
  .brand {
    position: absolute;
    inset: 0;
    display: flex;
    flex-direction: column;
    align-items: center;
    justify-content: center;
    gap: 6px;
  }
  .brand__mark {
    width: 16px; height: 16px;
    border-radius: 50%;
    background: var(--brand-green);
    margin-bottom: 10px;
  }
  .brand__name {
    font-family: "Cinzel", "Times New Roman", serif;
    font-weight: 600;
    color: var(--brand-blue);
    text-align: center;
    line-height: 1.25;
  }
  .brand__name-main { display: block; font-size: 38px; letter-spacing: 1px; }
  .brand__name-sub { display: block; font-size: 16px; letter-spacing: 4px; }
</style>
</head>
<body>
  <section class="card card--back" aria-label="Card back">
    <div class="identity">
      <p class="identity__name">Daniel Harlow</p>
      <p class="identity__role">Director</p>
    </div>
    <div class="divider"></div>
    <ul class="contact">
      <li class="contact__item">
        <svg class="contact__icon" viewBox="0 0 24 24" aria-hidden="true"><path fill="#8cc63f" d="M6.6 10.8a15.1 15.1 0 0 0 6.6 6.6l2.2-2.2c.3-.3.7-.4 1-.2 1.1.4 2.300.6 3.6.6.6 0 1 .4 1 1V20c0 .6-.4 1-1 1A17 17 0 0 1 3 4c0-.6.4-1 1-1h3.5c.6 0 1 .4 1 1 0 1.3.2 2.5.6 3.6.1.3 0 .7-.2 1z"/></svg>
        (555) 62Vista
      </li>
      <li class="contact__item">
        <svg class="contact__icon" viewBox="0 0 24 24" aria-hidden="true"><rect x="2" y="5" width="20" height="14" fill="none" stroke="#8cc63f" stroke-width="2"/><path d="M2 5l10 8 10-8" fill="none" stroke="#8cc63f" stroke-width="2"/></svg>
        sales@bramblefordyards.example
      </li>
      <li class="contact__item">
        <svg class="contact__icon" viewBox="0 0 24 24" aria-hidden="true"><circle cx="12" cy="12" r="10" fill="none" stroke="#8cc63f" stroke-width="2"/><path d="M2 12h20M12 2c3 3 3 17 0 20M12 2c-3 3-3 17 0 20" fill="none" stroke="#8cc63f" stroke-width="2"/></svg>
        www.bramblefordyards.example
      </li>
    </ul>
  </section>

  <section class="card card--front" aria-label="Card front">
    <div class="brand">
      <span class="brand__mark" aria-hidden="true"></span>
      <p class="brand__name">
        <span class="brand__name-main">Brambleford</span>
        <span class="brand__name-sub">Landscape Construction</span>
      </p>
    </div>
  </section>
</body>
</html>
```